business card deign

Logo needs the following on it.
1. attached logo
2. Tagline - "If it keeps a drink cold or the party going...we do it!"
3. Name- Dalton Pikes, Founder and CPO
4. Address - 412 E. Carver Avenue, Ste 2207, Tampa, FL. 33917
5. Phone - 555.318.4726

```html
<!DOCTYPE html>
<html lang="en">
<head>
<meta charset="utf-8">
<title>Hopley Business Card</title>
<link href="https://fonts.googleapis.com/css2?family=Roboto:wght@400;700;900&display=swap" rel="stylesheet">
<style>
  :root {
    --bg: #d6d6d6;
    --ink: #111111;
    --card-dark: #1a1a1a;
    --card-light: #ffffff;
    --text-light: #ffffff;
    --rule: #1a1a1a;
  }
  * { box-sizing: border-box; margin: 0; padding: 0; }
  html, body {
    width: 1200px; height: 711px; overflow: hidden;
    background: var(--bg);
    font-family: "Roboto", Arial, sans-serif;
  }
  .stage {
    width: 1200px; height: 711px;
    display: flex; align-items: center; justify-content: center; gap: 24px;
  }
  .card {
    position: relative;
    width: 560px; height: 320px;
    border-radius: 22px;
    overflow: hidden;
    box-shadow: 0 10px 24px rgba(0,0,0,.25);
  }
  .card--front {
    background: var(--card-dark);
    display: flex; align-items: center; justify-content: center;
  }
  .brand {
    display: flex; align-items: center; gap: 14px;
    font-weight: 900; letter-spacing: .32em;
  }
  .brand__dot { width: 14px; height: 14px; border-radius: 50%; }
  .card--front .brand { color: var(--text-light); font-size: 52px; }
  .card--front .brand__dot { background: var(--text-light); width: 20px; height: 20px; }

  .card--back { background: var(--card-light); color: var(--ink); }
  .card--back .brand {
    position: absolute; left: 34px; top: 96px;
    font-size: 34px; color: var(--ink);
  }
  .card--back .brand__dot { background: var(--ink); }
  .side-bar {
    position: absolute; right: 0; top: 44px;
    width: 18px; height: 62px; background: var(--ink);
  }
  .person {
    position: absolute; right: 34px; top: 46px; text-align: right;
  }
  .person__name { font-size: 27px; font-weight: 700; line-height: 1.1; }
  .person__title { font-size: 14px; font-weight: 400; margin-top: 4px; }
  .rule {
    position: absolute; left: 34px; right: 0; top: 164px;
    height: 1.5px; background: var(--rule);
  }
  .rule--title { left: auto; width: 210px; top: 108px; }
  .tagline {
    position: absolute; right: 34px; top: 186px;
    width: 220px; text-align: right;
    font-size: 12.5px; line-height: 1.5;
  }
  .contact {
    position: absolute; left: 34px; bottom: 30px;
    list-style: none; font-size: 13px; line-height: 1.45;
  }
  .contact__item { display: flex; gap: 10px; align-items: flex-start; }
  .contact__icon { width: 12px; height: 14px; margin-top: 3px; flex: none; }
</style>
</head>
<body>
<main class="stage">
  <section class="card card--front" aria-label="Card front">
    <div class="brand"><span class="brand__dot"></span><span>HOPLEY</span></div>
  </section>

  <section class="card card--back" aria-label="Card back">
    <div class="brand"><span class="brand__dot"></span><span>HOPLEY</span></div>
    <div class="side-bar"></div>
    <div class="person">
      <p class="person__name">Dalton Pikes</p>
      <p class="person__title">Founder and CPO</p>
    </div>
    <div class="rule rule--title"></div>
    <div class="rule"></div>
    <p class="tagline">If it keeps a drink cold or<br>the party going...we do it!</p>
    <ul class="contact">
      <li class="contact__item">
        <svg class="contact__icon" viewBox="0 0 24 24" aria-hidden="true"><path fill="#111" d="M6.6 10.8a15.1 15.1 0 0 0 6.6 6.6l2.2-2.2c.3-.3.7-.4 1-.2 1.1.4 2.3.6 3.6.6.6 0 1 .4 1 1V20c0 .6-.4 1-1 1A17 17 0 0 1 3 4c0-.6.4-1 1-1h3.5c.6 0 1 .4 1 1 0 1.3.2 2.5.6 3.6.1.3 0 .7-.2 1z"/></svg>
        <span>555.318.4726</span>
      </li>
      <li class="contact__item">
        <svg class="contact__icon" viewBox="0 0 24 24" aria-hidden="true"><path fill="none" stroke="#111" stroke-width="2.4" d="M12 22s-7-7.2-7-12.5a7 7 0 0 1 14 0C19 14.8 12 22 12 22z"/><circle cx="12" cy="9.5" r="2.6" fill="#111"/></svg>
        <span>412 E. Carver Avenue,<br>Ste 2207, Tampa, FL. 33917</span>
      </li>
    </ul>
  </section>
</main>
</body>
</html>
```